Business Card for beauty technology startup

Design Glimora Business Card for a Beauty, based on the website identity and colors (https://www.glimora-example.com).
Glimora is a beauty tech startup that gathers helpful product info for beauty lovers and consumers (such as availability on stores, price range and product reviews) for makeup products. The card design must be young, colorful but clean, and very modern.

Target Market(s)

woman, 15-35

Industry/Entity Type

Cosmetics

Contact Information for Business Card

Full Name, address, phone

Font styles to use
Other font styles liked:
• Advent Pro

Colors
e34297
86cfc6
ffffff
5c5c5c
e8e8e8
e667a6
b2b2b2

Requirements
Must have
• One full colored side with a creative design and another with card info
• Use Color palette: #95C5C5 and/or #D38AA5
• Use fonts: Advent Pro
• Use website identity: https://www.glimora-example.com
Nice to have
• If needed extra font: Roboto

```html
<!DOCTYPE html>
<html lang="en">
<head>
<meta charset="utf-8">
<title>Glimora Business Card</title>
<link rel="stylesheet" href="https://fonts.googleapis.com/css2?family=Barlow:wght@500;600&family=Lato:wght@400;700&display=swap">
<style>
  :root {
    --teal: #86cfc6;
    --paper: #ffffff;
    --ink: #2b2b2b;
    --ink-soft: #5c5c5c;
    --backdrop: #3a3a3c;
  }
  * { box-sizing: border-box; margin: 0; padding: 0; }
  html, body { width: 1200px; height: 926px; overflow: hidden; }
  body {
    background: var(--backdrop);
    display: flex;
    flex-direction: column;
    align-items: center;
    justify-content: center;
    gap: 60px;
    font-family: "Lato", sans-serif;
  }
  .card {
    position: relative;
    width: 620px;
    height: 360px;
    background: var(--paper);
    overflow: hidden;
    box-shadow: 0 10px 30px rgba(0,0,0,.35);
  }
  .card__band {
    position: absolute;
    top: 0; left: 0; bottom: 0;
    background: var(--teal);
  }
  .brand {
    display: flex;
    align-items: center;
    gap: 12px;
    color: var(--ink-soft);
    font-family: "Lato", sans-serif;
    font-weight: 400;
    font-size: 20px;
    letter-spacing: .2em;
    text-transform: uppercase;
    white-space: nowrap;
  }
  .brand__dot {
    width: 26px; height: 26px;
    border: 1.5px solid var(--ink-soft);
    border-radius: 50%;
  }

  /* Cover side */
  .card--cover .card__band { width: 57%; }
  .card--cover .brand { position: absolute; top: 44px; left: 40px; }
  .cover__url {
    position: absolute;
    right: 40px; bottom: 54px;
    display: flex; align-items: center; gap: 10px;
    font-family: "Barlow", sans-serif;
    font-weight: 500;
    font-size: 13px;
    letter-spacing: .3em;
    color: var(--ink);
    white-space: nowrap;
  }
  .cover__url::before {
    content: "";
    width: 26px; height: 1.5px;
    background: var(--ink);
  }

  /* Info side */
  .card--info .card__band { width: 42%; }
  .card--info .brand {
    position: absolute;
    left: 40px; bottom: 56px;
    transform: rotate(-90deg);
    transform-origin: left bottom;
    translate: 30px 0;
  }
  .info__name {
    position: absolute;
    left: 285px; top: 56px;
    padding-left: 12px;
    border-left: 2px solid var(--ink);
  }
  .info__name h1 {
    font-family: "Barlow", sans-serif;
    font-weight: 600;
    font-size: 21px;
    letter-spacing: .12em;
    color: var(--ink);
    line-height: 1.1;
    text-transform: uppercase;
    white-space: nowrap;
  }
  .info__name p {
    font-family: "Barlow", sans-serif;
    font-weight: 500;
    font-size: 9px;
    letter-spacing: .25em;
    color: var(--ink-soft);
    text-transform: uppercase;
  }
  .info__contact {
    position: absolute;
    left: 285px; top: 196px;
    list-style: none;
    color: var(--ink-soft);
    font-size: 15px;
    line-height: 22px;
  }
  .info__contact li { display: flex; align-items: center; gap: 10px; white-space: nowrap; }
  .info__contact svg { width: 14px; height: 14px; fill: var(--ink-soft); flex: none; }
  .info__address {
    position: absolute;
    left: 285px; top: 276px;
    color: var(--ink-soft);
    font-size: 15px;
    line-height: 22px;
    white-space: nowrap;
  }
</style>
</head>
<body>

  <section class="card card--cover">
    <div class="card__band"></div>
    <div class="brand"><span class="brand__dot"></span>Glimora</div>
    <div class="cover__url">WWW.GLIMORA-EXAMPLE.COM</div>
  </section>

  <section class="card card--info">
    <div class="card__band"></div>
    <div class="brand"><span class="brand__dot"></span>Glimora</div>
    <div class="info__name">
      <h1>Clara Whitfield</h1>
      <p>Title goes here</p>
    </div>
    <ul class="info__contact">
      <li>
        <svg viewBox="0 0 16 16"><path d="M3 2h3l1 3-2 1a8 8 0 0 0 5 5l1-2 3 1v3a1 1 0 0 1-1 1A13 13 0 0 1 2 3a1 1 0 0 1 1-1z"/></svg>
        555-014-7290
      </li>
      <li>
        <svg viewBox="0 0 16 16"><path d="M6.5 9.5l3-3M7 4l1.5-1.5a3 3 0 0 1 4.2 4.2L11 8.5M9 12l-1.5 1.5a3 3 0 0 1-4.2-4.2L5 7.5" stroke="#5c5c5c" stroke-width="1.6" fill="none" stroke-linecap="round"/></svg>
        www.glimora-example.com
      </li>
      <li>
        <svg viewBox="0 0 16 16"><path d="M1 3h14v10H1z"/><path d="M1 3l7 6 7-6" stroke="#fff" stroke-width="1.2" fill="none"/></svg>
        hello@glimora-example.com
      </li>
    </ul>
    <p class="info__address">48 Harbor Lane, Floor 2,<br>Unit 5B, Elm Court, CA 90417</p>
  </section>

</body>
</html>
```